Tidewell-Network Theme For Forums!

We are looking for a theme for our forums. The forums are ran off Invision Power Boards. We have a basic theme on there now but we want more our own feel. If possible have some longboarding accept incorporated in the theme. We want the theme to have some red in it to match our logo. Tidewell-network.com

Target Market(s)

Skatingboarding & Longboarding

Coding

Coded - Design and coding required

Number of Pages Required

1 page

Colors
f04a50

```html
<!DOCTYPE html>
<html lang="en">
<head>
<meta charset="utf-8">
<title>Tidewell-Network Forums</title>
<link rel="stylesheet" href="https://fonts.googleapis.com/css2?family=Mulish:wght@400;500;600;700;800&display=swap">
<style>
:root{
  --red:#e3001b;
  --black:#000;
  --white:#fff;
  --pink:#fdf0f1;
  --text:#1a1a1a;
  --muted:#5a5a5a;
  --line:#d9d9d9;
}
*{box-sizing:border-box;margin:0;padding:0}
html,body{width:1181px;height:1200px;overflow:hidden;background:var(--white);font-family:'Mulish',sans-serif;color:var(--text)}
.page{position:relative;width:1181px;height:1200px}
.abs{position:absolute}
.brand{left:29px;top:30px;display:flex;align-items:center;gap:12px;font-size:34px;font-weight:800;color:var(--red);letter-spacing:.5px}
.brand-mark{width:26px;height:26px;background:var(--red)}
.greeting{right:28px;top:52px;font-size:32px;color:var(--red);font-weight:500}
.topnav{left:0;top:105px;width:1181px;height:43px;background:var(--black);color:var(--white)}
.topnav .user{position:absolute;left:32px;top:5px}
.topnav .login{position:absolute;left:81px;top:12px;font-size:15px;font-weight:600}
.topnav .item{position:absolute;top:12px;font-size:15px;font-weight:600}
.topnav .search{position:absolute;left:1134px;top:13px}
.page-title{left:0;width:1181px;top:192px;text-align:center;font-size:16px;font-weight:800;letter-spacing:.3px}
.field{height:40px;background:var(--white);box-shadow:0 1px 4px rgba(0,0,0,.2);font-size:12.6px;color:var(--muted);padding:0 16px;line-height:40px}
.dots{position:absolute;right:16px;top:13px;width:3px}
.dots i{display:block;width:3px;height:3px;border-radius:50%;background:#999;margin-bottom:3px}
.go{left:1097px;top:250px;width:56px;height:31px;border-radius:16px;background:var(--red);border:2px solid #b0001a;box-shadow:0 0 0 1px #fff inset;color:var(--white);font-size:13px;font-weight:800;display:flex;align-items:center;justify-content:center;gap:4px}
.band{left:28px;width:1126px;height:42px;background:var(--red);color:var(--white);font-size:16.5px;font-weight:600;line-height:42px;padding-left:31px}
.band::before{content:"";position:absolute;left:12px;top:17px;width:7px;height:7px;border-radius:50%;background:var(--white)}
.band .toggle{position:absolute;right:12px;top:20px;width:9px;height:2px;background:var(--white)}
.cols{left:28px;top:363px;width:1126px;height:40px;background:var(--pink);border:1px solid #c98088;border-top:none;display:flex}
.cols div{border-right:1px solid #c98088;font-size:15px;font-weight:600;line-height:39px;padding-left:13px}
.cols div:last-child{border-right:none}
.row{left:28px;top:404px;width:1126px;height:113px;display:flex;gap:2px}
.row .cell{border:1px solid var(--line);height:113px;position:relative}
.num{font-size:13.5px;font-weight:700;text-align:center;line-height:111px}
.link{font-size:15px;font-weight:500;text-decoration:underline}
.small{font-size:12.6px;color:var(--muted)}
.hex{position:absolute}
.tabs{left:28px;top:645px;width:1126px;height:41px;display:flex}
.tabs div{font-size:15px;font-weight:600;line-height:41px;padding-left:13px;border-right:1px solid #c98088}
.tabs div:last-child{border-right:none}
.sub{left:28px;width:1126px;height:41px;background:var(--pink);font-size:13px;font-weight:600;line-height:41px;padding-left:31px}
.sub::before{content:"";position:absolute;left:12px;top:17px;width:7px;height:7px;border-radius:50%;background:var(--black)}
.body-text{font-size:12.6px;color:var(--muted);line-height:17px}
.detail{font-size:12.6px;color:var(--red);font-weight:700}
.detail a{color:var(--muted);font-weight:400;text-decoration:underline}
.now{right:45px;top:1117px;font-size:12.6px}
.footer{left:0;top:1150px;width:1181px;height:50px;background:var(--black);color:#ddd;font-size:12.6px;text-align:center;line-height:50px}
.footer .code{position:absolute;right:18px;top:0;font-size:13.5px;color:var(--white)}
</style>
</head>
<body>
<div class="page">
  <div class="abs brand"><span class="brand-mark"></span>Tidewell-Network</div>
  <div class="abs greeting">Welcome Guest !!</div>

  <nav class="abs topnav">
    <svg class="user" width="36" height="33" viewBox="0 0 36 33"><polygon points="9,1 27,1 36,16.5 27,32 9,32 0,16.5" fill="#fff"/><circle cx="18" cy="13" r="5" fill="#bbb"/><path d="M8 27c2-6 18-6 20 0" fill="#bbb"/></svg>
    <span class="login">Login Or Register</span>
    <span class="item" style="left:769px">Forum</span>
    <span class="item" style="left:855px">Member</span>
    <span class="item" style="left:961px">Calender</span>
    <span class="item" style="left:1067px">Blog</span>
    <svg class="search" width="16" height="16" viewBox="0 0 16 16"><circle cx="6.5" cy="6.5" r="4.8" fill="none" stroke="#fff" stroke-width="2.2"/><line x1="10" y1="10" x2="14.5" y2="14.5" stroke="#fff" stroke-width="2.6" stroke-linecap="round"/></svg>
  </nav>

  <h1 class="abs page-title">TIDEWELL-NETWORK</h1>

  <div class="abs field" style="left:30px;top:245px;width:444px">Welcome Back ; Your Last Visit Was : Today, 8.30 ,am<span class="dots"><i></i><i></i><i></i></span></div>
  <div class="abs field" style="left:659px;top:246px;width:208px">User Name</div>
  <div class="abs field" style="left:880px;top:246px;width:208px">Password</div>
  <div class="abs go">GO <svg width="14" height="9" viewBox="0 0 14 9"><path d="M0 4.5h11M8 1l4 3.5L8 8" fill="none" stroke="#fff" stroke-width="2"/></svg></div>

  <div class="abs band" style="top:321px">A TEST ROOT<span class="toggle"></span></div>
  <div class="abs cols">
    <div style="width:539px">Forum</div>
    <div style="width:142px;padding-left:20px">Topics</div>
    <div style="width:141px;padding-left:20px">Replies</div>
    <div style="width:304px;padding-left:21px">Last post Info</div>
  </div>
  <div class="abs row">
    <div class="cell" style="width:538px">
      <svg class="hex" style="left:22px;top:33px" width="48" height="44" viewBox="0 0 48 44"><polygon points="12,1 36,1 47,22 36,43 12,43 1,22" fill="var(--red)" stroke="#9c0013" stroke-width="1.5"/></svg>
      <div class="abs link" style="left:90px;top:32px">A Test Forum</div>
      <div class="abs small" style="left:90px;top:64px">A Test Forum May Be Removed At Any Time</div>
    </div>
    <div class="cell num" style="width:140px">1</div>
    <div class="cell num" style="width:140px">1</div>
    <div class="cell" style="width:302px">
      <div class="abs small" style="left:20px;top:34px;color:#333">April &amp;, 2018 , 8.30 pm</div>
      <div class="abs small" style="left:20px;top:64px;color:#333"><b style="color:var(--red);font-weight:600">In:</b>Welcome</div>
      <div class="abs small" style="right:18px;top:64px;color:#333"><b style="color:var(--red);font-weight:600">By:</b>TWN Team</div>
    </div>
  </div>

  <div class="abs field" style="left:710px;top:541px;width:444px">Delete Cookies Set By This Board.<span class="dots"><i></i><i></i><i></i></span></div>

  <div class="abs band" style="top:604px">BOARD STATISTICS<span class="toggle"></span></div>
  <div class="abs tabs">
    <div style="width:294px">Today's Active Topics</div>
    <div style="width:264px;padding-left:20px">The Moderating Team</div>
    <div style="width:264px;padding-left:17px">Today's Top 10 Posters</div>
    <div style="width:304px;padding-left:20px">Overall Top 10 Posters</div>
  </div>

  <div class="abs sub" style="top:686px">2 user(s) active in the past 15 minutes</div>
  <svg class="hex" style="left:51px;top:753px" width="48" height="44" viewBox="0 0 48 44"><polygon points="12,1 36,1 47,22 36,43 12,43 1,22" fill="var(--red)" stroke="#9c0013" stroke-width="1.5"/></svg>
  <div class="abs body-text" style="left:115px;top:751px">2 guests , 0 Members 0 Anonymous Members</div>
  <div class="abs detail" style="left:115px;top:776px">Show Detailed By : <a>Last Click</a> , <a>Member Name</a></div>

  <div class="abs sub" style="top:823px">Forthcoming Calendar Events Within The Next 5 days</div>
  <svg class="hex" style="left:51px;top:889px" width="48" height="44" viewBox="0 0 48 44"><polygon points="12,1 36,1 47,22 36,43 12,43 1,22" fill="var(--red)" stroke="#9c0013" stroke-width="1.5"/></svg>
  <div class="abs body-text" style="left:115px;top:903px">There are No Forthcoming Calendar Events</div>

  <div class="abs sub" style="top:960px">Board Statistics</div>
  <svg class="hex" style="left:51px;top:1026px" width="48" height="44" viewBox="0 0 48 44"><polygon points="12,1 36,1 47,22 36,43 12,43 1,22" fill="var(--red)" stroke="#9c0013" stroke-width="1.5"/></svg>
  <div class="abs body-text" style="left:115px;top:1011px;line-height:21px">Our Member Have made a total of 1 Posts<br>We have 1 Registered Members<br>The Newest member is Admin<br>Most Users ever online was 2 on Today,8.30 am</div>

  <div class="abs now">Time Is Now June 2, 2018 - 7.00 pm</div>

  <footer class="abs footer">© 2018 Copyrights.Tidewell Network.All Rights Reserved<span class="code">C28</span></footer>
</div>
</body>
</html>
```